UX - Need some screens design for a Skill Assessment Application

I am building an app to carry out skill assessments. Depending on how the assessment is configured, it may have one or more parts
1. Question based assessment (Multiple Choice, True False, Fill in the blanks"
2. Endorsement by two colleagues - A screen that allows user to pick colleagues based on search and shows the status of pending requests
3. A written submission - a page that explains the format of the submission and a file upload
As each assessment can be configured with or without any of the steps, the assessment UI must be such that these areas get hidden/displayed based on configuration.
Colour codes to be used can be #0e78bb and #ffffff
There will also be a start screen (instructions) and an end screen (results)
Target Market(s)
Enterprise software
Number of Pages Required
4 page

```html
<!DOCTYPE html>
<html lang="en">
<head>
<meta charset="utf-8">
<title>Application Design Capabilities – Assessment</title>
<link href="https://fonts.googleapis.com/css2?family=Inter:wght@400;500;600;700&display=swap" rel="stylesheet">
<style>
  :root {
    --brand: #0e78bb;
    --header: #0353a4;
    --white: #ffffff;
    --page: #f6f7f9;
    --band: #f1f2f4;
    --line: #dcdfe3;
    --ink: #262a30;
    --muted: #55595f;
    --faint: #c4c8cd;
    --link: #1a8fd0;
    --ring: #19a6e0;
  }
  * { box-sizing: border-box; margin: 0; padding: 0; }
  html, body { width: 1200px; height: 686px; overflow: hidden; }
  body { font-family: "Inter", sans-serif; background: var(--page); color: var(--ink); position: relative; }
  .abs { position: absolute; }

  .topbar { position: absolute; left: 0; top: 0; width: 1200px; height: 43px; background: var(--header); }
  .brand { left: 57px; top: 12px; display: flex; align-items: center; gap: 8px; color: var(--white); font-size: 15px; font-weight: 600; }
  .brand-dot { width: 18px; height: 18px; border-radius: 50%; background: var(--white); }
  .nav a { position: absolute; top: 15px; font-size: 12px; color: #c9d8ec; text-decoration: none; }
  .nav a.active { color: var(--white); font-weight: 600; }
  .avatar { left: 1102px; top: 8px; width: 26px; height: 26px; border-radius: 50%; background: linear-gradient(135deg, #6b4a3c, #c79a80); }
  .chevron { left: 1134px; top: 16px; }

  .pagehead { position: absolute; left: 0; top: 43px; width: 1200px; height: 97px; background: var(--white); }
  .crumbs { left: 57px; top: 65px; display: flex; align-items: center; font-size: 11px; color: var(--muted); }
  .crumbs a { color: var(--link); text-decoration: none; margin-left: 12px; }
  .crumbs .sep { margin: 0 7px; }
  .updated { right: 88px; top: 68px; font-size: 11px; color: var(--muted); }
  .updated b { color: var(--ink); font-weight: 500; }
  .title-icon { left: 88px; top: 101px; }
  .title { left: 123px; top: 98px; font-size: 20.5px; font-weight: 600; color: var(--ink); }
  .btn { position: absolute; display: flex; align-items: center; justify-content: center; font-size: 11px; border-radius: 3px; }
  .btn-outline { background: var(--white); border: 1px solid var(--brand); color: var(--brand); }
  .btn-solid { background: var(--brand); color: var(--white); }
  .save { left: 1008px; top: 96px; width: 104px; height: 31px; }

  .meta { position: absolute; left: 0; top: 140px; width: 1200px; height: 45px; background: var(--band); border-top: 1px solid var(--line); border-bottom: 1px solid var(--line); }
  .meta-item { position: absolute; top: 16px; font-size: 10px; color: var(--ink); }
  .meta-item .v { color: var(--link); }
  .meta-item .g { color: var(--muted); }
  .meta-div { position: absolute; top: 15px; width: 1px; height: 14px; background: var(--line); }
  .ring { left: 1053px; top: 149px; }
  .count { left: 1089px; top: 157px; font-size: 10.5px; color: var(--muted); }
  .count b { color: var(--ink); }

  .qnum { left: 367px; top: 220px; font-size: 14.5px; color: #7a7f86; }
  .qtext { position: absolute; font-size: 14.5px; color: var(--ink); }
  .blank { position: absolute; height: 36px; border-bottom: 1px solid var(--line); font-size: 14.5px; color: var(--faint); padding-top: 8px; }
  .divider { left: 367px; top: 372px; width: 467px; height: 1px; background: var(--line); }
  .back { left: 366px; top: 400px; width: 72px; height: 31px; }
  .submit { left: 726px; top: 400px; width: 108px; height: 31px; }
</style>
</head>
<body>
  <header class="topbar">
    <div class="abs brand"><span class="brand-dot"></span>Assessly</div>
    <nav class="nav">
      <a class="active" href="#" style="left:752px">Assessments</a>
      <a href="#" style="left:852px">Endorsement</a>
      <a href="#" style="left:948px">Submissions</a>
      <a href="#" style="left:1040px">Results</a>
    </nav>
    <div class="abs avatar" role="img" aria-label="User profile photo"></div>
    <svg class="abs chevron" width="10" height="7" viewBox="0 0 10 7"><path d="M1 1l4 4 4-4" fill="none" stroke="#fff" stroke-width="1.6"/></svg>
  </header>

  <section class="pagehead"></section>
  <div class="abs crumbs">
    <svg width="19" height="19" viewBox="0 0 20 20"><circle cx="10" cy="10" r="8.8" fill="none" stroke="#0e78bb" stroke-width="1.6"/><path d="M14.5 10H6.5M9.5 6.8L6.3 10l3.2 3.2" fill="none" stroke="#0e78bb" stroke-width="1.6"/></svg>
    <a href="#">Assessment</a><span class="sep">/</span><span>Application Design Capabilities</span>
  </div>
  <div class="abs updated">Last Updated: <b>17/05/2024</b></div>
  <svg class="abs title-icon" width="22" height="22" viewBox="0 0 22 22">
    <rect x="2" y="1.5" width="14" height="18" rx="1.5" fill="none" stroke="#555" stroke-width="1.6"/>
    <path d="M5 6h2M9 6h4M5 10h2M9 10h4M5 14h2" stroke="#555" stroke-width="1.5"/>
    <circle cx="16" cy="16" r="4.5" fill="#555"/><path d="M14 16l1.5 1.5 2.5-2.5" fill="none" stroke="#fff" stroke-width="1.3"/>
  </svg>
  <h1 class="abs title">Application Design Capabilities</h1>
  <a class="btn btn-outline save" href="#">Save Progress</a>

  <section class="meta">
    <div class="meta-item" style="left:88px">Assessment Date: <span class="v">September 23, 2024</span></div>
    <div class="meta-div" style="left:301px"></div>
    <div class="meta-item" style="left:322px">Assessment Type: <span class="v">UI/UX Skill</span></div>
    <div class="meta-div" style="left:486px"></div>
    <div class="meta-item" style="left:507px">Assessment Responses: <span class="g">7 of 8 Responded / Closed: in next 4 month</span></div>
  </section>
  <svg class="abs ring" width="28" height="28" viewBox="0 0 28 28"><circle cx="14" cy="14" r="12.5" fill="none" stroke="#19a6e0" stroke-width="2.6"/></svg>
  <div class="abs count"><b>8</b> / 8</div>

  <main>
    <div class="abs qnum">Q.8.</div>
    <span class="qtext" style="left:414px;top:220px">How do you</span>
    <div class="blank" style="left:512px;top:215px;width:162px">Type a label</div>
    <span class="qtext" style="left:680px;top:220px">in</span>
    <div class="blank" style="left:704px;top:215px;width:130px">Type a label</div>

    <span class="qtext" style="left:414px;top:266px">This is a fill in the</span>
    <div class="blank" style="left:553px;top:261px;width:161px">blanks</div>
    <span class="qtext" style="left:724px;top:266px">field. Please</span>

    <span class="qtext" style="left:414px;top:312px">sign your name:</span>
    <div class="blank" style="left:553px;top:307px;width:161px">here</div>
    <span class="qtext" style="left:724px;top:312px">. Thank you</span>

    <div class="abs divider"></div>
    <a class="btn btn-outline back" href="#">Go Back</a>
    <a class="btn btn-solid submit" href="#">Submit Answer</a>
  </main>
</body>
</html>
```